Carpet cleaning company focused on high quality needs business cards

We are a growing company that just merged with another company and need to design a new business card. We do both residential as well as commercial cleaning. We do carpet, tile & grout, upholstery, hard floors, and stain & pet odor removal. We treat our customers like family and strive to achieve outstanding results with every job.

```html
<!DOCTYPE html>
<html lang="en">
<head>
<meta charset="utf-8">
<title>Brightwell Floor Care – Business Card</title>
<link rel="stylesheet" href="https://fonts.googleapis.com/css2?family=Poppins:wght@400;700&family=Source+Sans+3:wght@600&family=Roboto+Condensed:wght@700&display=swap">
<style>
  :root {
    --brand-red: #ef4641;
    --ink: #231f20;
    --text-grey: #2f2f35;
    --card-white: #ffffff;
    --backdrop: #8a8a8a;
    --mascot-blue: #2a7fc1;
    --mascot-tan: #c9a064;
  }
  * { box-sizing: border-box; margin: 0; padding: 0; }
  html, body { width: 1093px; height: 1200px; overflow: hidden; }
  body {
    background: var(--backdrop);
    position: relative;
    font-family: "Poppins", sans-serif;
  }
  .card {
    position: absolute;
    left: 265px;
    width: 580px;
    height: 356px;
    border-radius: 27px;
    overflow: hidden;
  }
  .card-front { top: 226px; background: var(--card-white); }
  .card-back { top: 621px; background: var(--brand-red); }

  /* front */
  .faint-mascot {
    position: absolute;
    left: 0; top: 0;
    width: 280px; height: 356px;
    background: radial-gradient(ellipse at 40% 55%, rgba(225,232,240,0.7), rgba(245,245,245,0.25) 60%, rgba(255,255,255,0) 80%);
  }
  .holder-name {
    position: absolute; left: 31px; top: 43px;
    font-weight: 700; font-size: 24px; line-height: 1;
    color: var(--brand-red);
  }
  .holder-title {
    position: absolute; left: 32px; top: 72px;
    font-size: 17px; line-height: 1; color: var(--text-grey);
  }
  .front-illustration {
    position: absolute; left: 284px; top: 22px;
    width: 120px; height: 140px;
    background: linear-gradient(160deg, var(--mascot-blue) 0%, var(--mascot-tan) 55%, var(--brand-red) 100%);
    opacity: 0.9;
  }
  .wordmark {
    position: absolute;
    font-weight: 700;
    line-height: 1.1;
    white-space: nowrap;
  }
  .wordmark-front { left: 415px; top: 90px; font-size: 24px; color: var(--ink); }
  .contact-list {
    position: absolute; left: 31px; top: 255px;
    list-style: none;
  }
  .contact-item {
    display: flex; align-items: center; gap: 6px;
    height: 24px;
    font-size: 17px; color: var(--text-grey);
  }
  .contact-icon { width: 22px; height: 22px; flex: none; }
  .address {
    position: absolute; right: 36px; top: 280px;
    text-align: right; font-size: 17px; line-height: 21px; color: var(--text-grey);
  }

  /* back */
  .back-illustration {
    position: absolute; left: 102px; top: 31px;
    width: 170px; height: 196px;
    background: linear-gradient(170deg, #ffffff 0%, var(--mascot-blue) 45%, var(--mascot-tan) 75%, #ffffff 100%);
  }
  .wordmark-back { left: 287px; top: 128px; font-size: 36px; color: #ffffff; }
  .service-band {
    position: absolute; left: 0; top: 253px;
    width: 100%; height: 48px;
    background: var(--card-white);
    display: flex; align-items: center; justify-content: center;
    font-family: "Source Sans 3", sans-serif; font-weight: 600;
    font-size: 22px; color: var(--ink);
  }
  .service-list {
    position: absolute; left: 0; top: 306px; width: 100%;
    text-align: center;
    font-family: "Roboto Condensed", sans-serif; font-weight: 700;
    font-size: 18.5px; letter-spacing: -0.4px; color: #ffffff;
  }
</style>
</head>
<body>
  <section class="card card-front">
    <div class="faint-mascot" role="img" aria-label="Faint oversized mascot illustration of a smiling cleaner holding a steam wand"></div>
    <h1 class="holder-name">Marcus Hale</h1>
    <p class="holder-title">Managing Director</p>
    <div class="front-illustration" role="img" aria-label="Mascot illustration of a cleaner in cap and blue shirt raising a steam wand"></div>
    <p class="wordmark wordmark-front">Brightwell<br>Floor Care</p>
    <ul class="contact-list">
      <li class="contact-item">
        <svg class="contact-icon" viewBox="0 0 22 22"><circle cx="11" cy="11" r="10" fill="none" stroke="#ef4641" stroke-width="1.4"/><path d="M7.5 6.5c.6-.6 1.3-.4 1.6.2l.8 1.5c.2.5 0 .9-.4 1.2l-.5.4c.6 1.3 1.6 2.3 2.9 2.9l.4-.5c.3-.4.7-.6 1.2-.4l1.5.8c.6.3.8 1 .2 1.6-.9 1-2.3 1.2-3.6.5-2-1.1-3.5-2.6-4.6-4.6-.7-1.3-.5-2.7.5-3.6z" fill="#ef4641"/></svg>
        055-987 210 346
      </li>
      <li class="contact-item">
        <svg class="contact-icon" viewBox="0 0 22 22"><circle cx="11" cy="11" r="10" fill="none" stroke="#ef4641" stroke-width="1.4"/><rect x="6" y="7.5" width="10" height="7" rx="1" fill="#ef4641"/><path d="M6.3 8l4.7 3.6L15.7 8" fill="none" stroke="#fff" stroke-width="1"/></svg>
        hello@brightwellcare.com
      </li>
      <li class="contact-item">
        <svg class="contact-icon" viewBox="0 0 22 22"><circle cx="11" cy="11" r="10" fill="none" stroke="#ef4641" stroke-width="1.4"/><g fill="none" stroke="#ef4641" stroke-width="1"><circle cx="11" cy="11" r="5"/><ellipse cx="11" cy="11" rx="2.2" ry="5"/><path d="M6 11h10M6.8 8.5h8.4M6.8 13.5h8.4"/></g></svg>
        www.brightwellcare.com
      </li>
    </ul>
    <p class="address">88 Linden Row, Suite 4<br>Brookfield, 30917</p>
  </section>

  <section class="card card-back">
    <div class="back-illustration" role="img" aria-label="Mascot illustration of a cheerful cleaner with a steam wand on a white burst panel"></div>
    <p class="wordmark wordmark-back">Brightwell<br>Floor Care</p>
    <p class="service-band">RESIDENTIAL &amp; COMMERCIAL CLEANING</p>
    <p class="service-list">Carpet • Tile &amp; Grout • Upholstery • Hard floors &amp; Stain • Pet Odor Removal</p>
  </section>
</body>
</html>
```